Sustainably Transforming Education

Company is education services based. early learning through adult and corporate. Focus is national government policy and program design and delivery alongside a research based and academically grounded set of approaches to planning, evaluation, and change management.I am looking for an innovative design position that aligns with the global agendas for innovation, creativity and collaboration at international and national policy levels (berulo is a name that reflects these qualities - colours need to reflect amythyst in some way). I also need a design that translates from a business card as 1 medium of interaction to a template that can work in word/powerpoint etc to support both stationery as well as a digital strategy across multiple channels (fb/twit/etc)There is no slogan/tag line for the company and their is no logo. I was looking to just leverage the name - have currently played around with various fonts (ending up with cuisine - all lowercase).

Industry/Entity Type

Adult

Contact Information for Business Card

name: berulo (all lowercase)Chairman: Andrew CrowMobile: +61 418 902 131Web: www.berulo.comemail: martin.pelly@berulo-example.com

Font styles to use
Script
Other font styles liked:
• cuisine

Colors
e34298
e667a6
33a6d7
aaaaaa

Requirements
Nice to have
• https://files.example-share.net/sh/qx7kw2hd91lzmnp/AAFr3tYbQeLp8VwZnKcDs2Hu?dl=0
• Link to the printwell templates used to begin this process....the one with the lines was about people intersecting (collaborating).....the organic shapes one more of a fluid feel of people coming together - the overall shape being largely spherical could represent a "global" feel.....anyway that is how I was thinking about these

```html
<!DOCTYPE html>
<html lang="en">
<head>
<meta charset="utf-8">
<title>berulo – Business Card</title>
<link rel="stylesheet" href="https://fonts.googleapis.com/css2?family=Kaushan+Script&display=swap">
<style>
  :root {
    --amethyst: #e34298;
    --amethyst-light: #e667a6;
    --sky: #33a6d7;
    --stone: #aaaaaa;
    --stone-deep: #9a9a9d;
    --ink: #1a1a1a;
    --paper: #ffffff;
    --script: "Kaushan Script", cursive;
  }
  html, body {
    margin: 0;
    padding: 0;
    width: 1200px;
    height: 740px;
    overflow: hidden;
    background: var(--paper);
  }
  .card {
    position: relative;
    width: 1200px;
    height: 740px;
    overflow: hidden;
    background: var(--amethyst);
    font-family: var(--script);
  }
  .card-shapes {
    position: absolute;
    inset: 0;
  }
  .shape-stone { fill: var(--stone); }
  .shape-band { fill: var(--amethyst-light); }
  .map-area {
    position: absolute;
    left: 326px;
    top: 206px;
    width: 598px;
    height: 344px;
    border-radius: 46% 40% 38% 44% / 36% 34% 52% 48%;
    background: radial-gradient(ellipse at 50% 45%, var(--stone-deep) 0%, rgba(154,154,157,0.55) 60%, rgba(170,170,170,0) 100%);
  }
  .holder-name {
    position: absolute;
    left: 136px;
    top: 72px;
    margin: 0;
    font-size: 72px;
    font-weight: 400;
    line-height: 1;
    color: var(--paper);
  }
  .holder-role {
    position: absolute;
    left: 420px;
    top: 166px;
    margin: 0;
    font-size: 40px;
    line-height: 1;
    color: var(--ink);
  }
  .divider {
    position: absolute;
    left: 326px;
    top: 227px;
    width: 760px;
    height: 3px;
    background: var(--sky);
  }
  .contact-list {
    position: absolute;
    left: 524px;
    top: 360px;
    margin: 0;
    padding: 0;
    list-style: none;
  }
  .contact-item {
    display: flex;
    align-items: center;
    height: 58px;
    font-size: 32px;
    color: var(--paper);
  }
  .contact-icon {
    width: 28px;
    height: 28px;
    margin-right: 24px;
    flex: none;
  }
  .contact-icon * { fill: var(--amethyst); }
  .contact-icon .stroke { fill: none; stroke: var(--amethyst); stroke-width: 2; }
  .brand-name {
    position: absolute;
    left: 72px;
    top: 556px;
    margin: 0;
    font-size: 92px;
    line-height: 1;
    color: var(--paper);
  }
</style>
</head>
<body>
<main class="card">
  <svg class="card-shapes" viewBox="0 0 1200 740" width="1200" height="740" aria-hidden="true">
    <path class="shape-stone" d="M0,0 L430,0 C700,40 1050,220 1200,500 L1200,740 L670,740 C450,600 150,380 0,90 Z"/>
    <path class="shape-band" d="M430,0 C760,12 1080,200 1200,330 L1200,500 C1050,220 700,40 430,0 Z"/>
  </svg>

  <div class="map-area" role="img" aria-label="Faint world map behind the contact details"></div>

  <h1 class="holder-name">Martin Pelly</h1>
  <p class="holder-role">Chairman</p>
  <div class="divider"></div>

  <ul class="contact-list">
    <li class="contact-item">
      <svg class="contact-icon" viewBox="0 0 28 28" aria-hidden="true">
        <path d="M3,9 C3,5 8,3 14,3 C20,3 25,5 25,9 L25,11 L19,11 L19,8 L9,8 L9,11 L3,11 Z"/>
        <path d="M7,12 L21,12 L24,24 L4,24 Z"/>
      </svg>
      <span>+61 427 315 086</span>
    </li>
    <li class="contact-item">
      <svg class="contact-icon" viewBox="0 0 28 28" aria-hidden="true">
        <rect x="2" y="6" width="24" height="17"/>
        <path class="stroke" style="stroke:#aaaaaa" d="M2,6 L14,16 L26,6 M2,23 L11,14 M26,23 L17,14"/>
      </svg>
      <span>martin.pelly@berulo-example.com</span>
    </li>
    <li class="contact-item">
      <svg class="contact-icon" viewBox="0 0 28 28" aria-hidden="true">
        <circle class="stroke" cx="14" cy="14" r="11"/>
        <ellipse class="stroke" cx="14" cy="14" rx="5" ry="11"/>
        <path class="stroke" d="M3,14 L25,14 M5,8 L23,8 M5,20 L23,20 M14,3 L14,25"/>
      </svg>
      <span>www.berulo-example.com</span>
    </li>
  </ul>

  <p class="brand-name">berulo</p>
</main>
</body>
</html>
```